Film poster for a contemporary thriller/chase film set in Italy/Capri/Croatia

This is a poster to initially publicize the feature film, Marden's Lantern. This may become the final poster for the film but at the moment it will be used just to promote it to investors through film festivals, etc. The poster must have a sense of urgency since the film is fast-paced. Examples include Pellweather films, Harbor of Ashes, Vesko, Kettler Ledger, Vellum of Ember.

Target Market(s)

Film investors, film lovers, talent agents

Industry/Entity Type

Film Production

Font styles to use
Serif

Colors

Designer to choose colors to be used in the design.

Requirements
Must have
• This is a thriller film set in modern-day Italy, Capri, and Croatia. The plot involves a young woman discovering a 2,000-year-old ring in a sea cliff on Capri. The ring was Orvallo's wedding ring and historians and others have looked for it for centuries. The woman must evade criminals, antiquities collectors, and the Vatican in an attempt to return it to its rightful heir. ELEMENTS: The mediteranean Sea, Orvallo, a gold ring with a single emerald.
Nice to have
• The idea of a woman being chased across Italy. I can supply images of the actresses's faces if that helps.
Should not have
• Cannot thik of any!

```html
<!DOCTYPE html>
<html lang="en">
<head>
<meta charset="utf-8">
<title>Marden's Lantern — Poster</title>
<link rel="stylesheet" href="https://fonts.googleapis.com/css2?family=Germania+One&display=swap">
<style>
  :root {
    --ink: #0f0d0d;
    --amber: #f6961e;
    --crimson: #8a0b06;
    --oxblood: #3a0808;
    --umber: #5e3d10;
    --shadow-figure: #1a0c08;
  }
  html, body {
    margin: 0;
    padding: 0;
    width: 848px;
    height: 1200px;
    overflow: hidden;
    background: var(--ink);
  }
  .poster {
    display: block;
    width: 848px;
    height: 1200px;
    background: var(--ink);
  }
  .band-ink { fill: var(--ink); }
  .band-amber { fill: var(--amber); }
  .band-crimson { fill: var(--crimson); }
  .band-oxblood { fill: var(--oxblood); }
  .band-umber { fill: var(--umber); }
  .ring-badge { fill: var(--ink); }
  .runner-figure { fill: var(--shadow-figure); opacity: 0.85; }
  .film-title {
    font-family: "Germania One", cursive;
    font-size: 96px;
    fill: var(--amber);
    letter-spacing: 2px;
  }
  .tagline {
    font-family: "Germania One", cursive;
    font-size: 34px;
    fill: var(--ink);
    letter-spacing: 1px;
  }
  .credits {
    font-family: "Germania One", cursive;
    font-size: 21px;
    fill: var(--ink);
  }
</style>
</head>
<body>
<svg class="poster" viewBox="0 0 794 1123" preserveAspectRatio="none" xmlns="http://www.w3.org/2000/svg">

  <!-- chevron stack, outermost first -->
  <g class="chevrons">
    <polygon class="band-crimson" points="-925,-600 275,600 1475,-600 1475,-1400 -925,-1400"/>
    <polygon class="band-oxblood" points="-925,-800 275,400 1475,-800 1475,-1400 -925,-1400"/>
    <polygon class="band-ink" points="-925,-820 275,380 1475,-820 1475,-1400 -925,-1400"/>
    <polygon class="band-amber" points="-925,-880 275,320 1475,-880 1475,-1400 -925,-1400"/>
    <polygon class="band-ink" points="-925,-1020 275,180 1475,-1020 1475,-1400 -925,-1400"/>
    <polygon class="band-umber" points="-925,-1050 275,150 1475,-1050 1475,-1400 -925,-1400"/>
    <polygon class="band-ink" points="-925,-1075 275,125 1475,-1075 1475,-1400 -925,-1400"/>
    <polygon class="band-crimson" points="-925,-1110 275,90 1475,-1110 1475,-1400 -925,-1400"/>
  </g>

  <!-- lower stepped bands running down-right, with staggered square ends -->
  <g class="stepped-bands" transform="rotate(45)">
    <rect class="band-oxblood" x="0" y="290" width="660" height="14"/>
    <rect class="band-ink" x="0" y="304" width="640" height="30"/>
    <rect class="band-amber" x="0" y="334" width="830" height="136"/>
    <rect class="band-umber" x="0" y="470" width="880" height="22"/>
    <rect class="band-oxblood" x="0" y="492" width="1120" height="74"/>
    <rect class="band-crimson" x="0" y="492" width="1090" height="68"/>
    <rect class="band-ink" x="0" y="566" width="1150" height="26"/>
    <rect class="band-amber" x="0" y="592" width="1200" height="80"/>
    <rect class="band-umber" x="0" y="672" width="1260" height="22"/>
    <rect class="band-ink" x="0" y="694" width="1300" height="26"/>
    <rect class="band-oxblood" x="0" y="720" width="1400" height="60"/>
    <rect class="band-crimson" x="0" y="720" width="1370" height="56"/>
    <rect class="band-ink" x="0" y="780" width="1440" height="26"/>
    <rect class="band-umber" x="0" y="806" width="1500" height="22"/>
    <rect class="band-amber" x="0" y="828" width="1560" height="80"/>
    <rect class="band-ink" x="0" y="908" width="1620" height="30"/>
    <rect class="band-crimson" x="0" y="938" width="1700" height="80"/>

    <!-- credits set on the crimson band -->
    <g class="credits">
      <text x="820" y="525" text-anchor="middle">MIRELLA VANTOSI, ODETTA LUNRAVE,</text>
      <text x="820" y="550" text-anchor="middle">TOBIN HARLE</text>
    </g>
  </g>

  <!-- ring badges -->
  <circle class="ring-badge" cx="410" cy="95" r="38" role="img" aria-label="Gold ring icon"/>
  <circle class="ring-badge" cx="75" cy="375" r="40" role="img" aria-label="Gold ring icon"/>
  <circle class="ring-badge" cx="232" cy="880" r="36" role="img" aria-label="Gold ring icon"/>

  <!-- running woman silhouettes -->
  <rect class="runner-figure" x="215" y="215" width="90" height="110" rx="30" role="img" aria-label="Silhouette of a woman running"/>
  <rect class="runner-figure" x="150" y="445" width="110" height="130" rx="34" role="img" aria-label="Silhouette of a woman running"/>
  <rect class="runner-figure" x="50" y="580" width="95" height="130" rx="30" role="img" aria-label="Silhouette of a woman running"/>

  <!-- tagline along the crimson band -->
  <text class="tagline" x="545" y="285" text-anchor="middle" transform="rotate(-45 545 285)">A 2000-YEAR-OLD MYSTERY</text>

  <!-- title -->
  <text class="film-title" x="590" y="645" text-anchor="middle">MARDEN'S</text>
  <text class="film-title" x="590" y="775" text-anchor="middle">LANTERN</text>
</svg>
</body>
</html>
```